RW Framewell Inc Business cards

We need business cards using our existing logo but slightly modified. Right now the logo says RW Loadbearing Masonry. We want to keep the RW part of the design, but replace the Structural Concrete portion with "FRAMEWELL". Please see the attached file.
Ideally this would be a blank template so we can add Different Names, titles, and phone numbers later.
On the one side we want only the logo and on the other side the detail. I'm attaching an example for you to see.
Please reach out with any other questions. Our address and other details will be given out once we find a design we like.

Target Market(s)

Construction Industry

```html
<!DOCTYPE html>
<html lang="en">
<head>
<meta charset="utf-8">
<title>RW Framewell Inc – Business Cards</title>
<link rel="stylesheet" href="https://fonts.googleapis.com/css2?family=Questrial&family=Open+Sans:wght@400;600&display=swap">
<style>
  :root {
    --stage: #262626;
    --brand-blue: #1474c0;
    --brand-blue-light: #2a86cf;
    --paper: #ffffff;
    --band-grey: #838486;
    --text-grey: #6b6b6b;
    --white: #ffffff;
  }
  * { box-sizing: border-box; margin: 0; padding: 0; }
  html, body { width: 1200px; height: 900px; overflow: hidden; }
  body {
    background: var(--stage);
    font-family: "Open Sans", sans-serif;
    position: relative;
  }
  .card {
    position: absolute;
    left: 300px;
    width: 600px;
    height: 343px;
    overflow: hidden;
  }
  .card--front { top: 70px; background: var(--brand-blue); }
  .card--back { top: 470px; background: var(--paper); }

  .front-texture {
    position: absolute; inset: 0;
    background: linear-gradient(135deg, var(--brand-blue-light), var(--brand-blue) 60%);
  }
  .wordmark {
    position: absolute;
    display: flex; align-items: baseline; gap: 14px;
    font-family: "Questrial", sans-serif;
    color: var(--white);
    letter-spacing: 0.04em;
    white-space: nowrap;
  }
  .card--front .wordmark { left: 50%; top: 50%; transform: translate(-50%, -50%); }
  .wordmark__initials { font-size: 54px; }
  .wordmark__name { font-size: 30px; }

  .back-header {
    position: absolute; left: 0; top: 0; width: 100%; height: 112px;
    background: var(--brand-blue);
  }
  .back-header .wordmark { left: 50%; top: 50%; transform: translate(-50%, -50%); }
  .back-header .wordmark__initials { font-size: 46px; }
  .back-header .wordmark__name { font-size: 26px; }

  .person {
    position: absolute; right: 322px; top: 158px;
    text-align: right;
  }
  .person__name {
    font-family: "Questrial", sans-serif;
    font-size: 30px; color: var(--brand-blue);
    letter-spacing: 0.03em; word-spacing: 0.3em;
    line-height: 1;
  }
  .person__title { font-size: 17px; color: var(--text-grey); margin-top: 2px; }

  .divider {
    position: absolute; left: 300px; top: 150px;
    width: 2px; height: 96px; background: var(--brand-blue);
  }

  .contact-list {
    position: absolute; left: 320px; top: 152px;
    list-style: none;
  }
  .contact-list li {
    display: flex; align-items: center; gap: 10px;
    font-size: 16px; color: var(--text-grey);
    height: 23px;
  }
  .contact-list svg { width: 16px; height: 16px; fill: var(--brand-blue); flex: none; }

  .address-band {
    position: absolute; left: 0; bottom: 26px; width: 100%; height: 38px;
    background: var(--band-grey);
    color: var(--white);
    font-size: 16px; text-align: center; line-height: 38px;
  }
</style>
</head>
<body>

<section class="card card--front" aria-label="Card front">
  <div class="front-texture" role="img" aria-label="Faint repeated brand pattern across the card"></div>
  <div class="wordmark">
    <span class="wordmark__initials">RW</span>
    <span class="wordmark__name">FRAMEWELL</span>
  </div>
</section>

<section class="card card--back" aria-label="Card back">
  <header class="back-header">
    <div class="wordmark">
      <span class="wordmark__initials">RW</span>
      <span class="wordmark__name">FRAMEWELL</span>
    </div>
  </header>

  <div class="person">
    <p class="person__name">ALEX MORGAN</p>
    <p class="person__title">Chief Officer</p>
  </div>

  <div class="divider"></div>

  <ul class="contact-list">
    <li>
      <svg viewBox="0 0 16 16" aria-hidden="true"><path d="M3.6 1.2l2.3 2.6-1.4 1.8c.9 2 2.5 3.7 4.6 4.8l1.7-1.4 2.7 2.3-1.6 2.3C6.8 13 2.7 9 1.4 3.2z"/></svg>
      +00 8 38 00 00
    </li>
    <li>
      <svg viewBox="0 0 16 16" aria-hidden="true"><path d="M4.5 0.5h7a1 1 0 0 1 1 1v13a1 1 0 0 1-1 1h-7a1 1 0 0 1-1-1v-13a1 1 0 0 1 1-1zM5 2.5v9.5h6V2.5zM8 12.8a.9.9 0 1 0 0 1.8.9.9 0 0 0 0-1.8z"/></svg>
      +00 0 90 00 00
    </li>
    <li>
      <svg viewBox="0 0 16 16" aria-hidden="true"><path d="M1 3h14v10H1zM2.5 4.5L8 8.8l5.5-4.3v-.1h-11zM2.5 6.3v5.2h11V6.3L8 10.6z"/></svg>
      info@rwframewell.com
    </li>
    <li>
      <svg viewBox="0 0 16 16" aria-hidden="true"><path d="M8 1a7 7 0 1 0 0 14A7 7 0 0 0 8 1zm-1 1.6C6 3.8 5.4 5.6 5.3 7.3H2.6A5.5 5.5 0 0 1 7 2.6zm2 0a5.5 5.5 0 0 1 4.4 4.7h-2.7C10.6 5.6 10 3.8 9 2.6zM8 2.9c.9 1.2 1.4 2.7 1.5 4.4h-3c.1-1.7.6-3.2 1.5-4.4zM2.6 8.7h2.7c.1 1.7.7 3.5 1.7 4.7A5.5 5.5 0 0 1 2.6 8.7zm3.9 0h3c-.1 1.7-.6 3.2-1.5 4.4-.9-1.2-1.4-2.7-1.5-4.4zm4.2 0h2.7A5.5 5.5 0 0 1 9 13.4c1-1.2 1.6-3 1.7-4.7z"/></svg>
      www.rwframewell.com
    </li>
  </ul>

  <footer class="address-band">Your address line here. Country/ State</footer>
</section>

</body>
</html>
```